Jolly Paws Business Card Update

I have a business card which I love. I want to keep the same logo, colours, font and style. I want to upgrade the scripting and remove some elements and add others.
On the front side under Services - remove the existing wording and insert - Providing individual coaching strategies to create happy, healthy and social canine companions
Under Denise Carvell amend the current wording to read: Qualified in Dog Behavioural Training, Natural Animal Healthcare and Animal Health Science
On the reverse side to remove the web address.

```html
<!DOCTYPE html>
<html lang="en">
<head>
<meta charset="utf-8">
<title>Jolly Paws Business Card</title>
<link href="https://fonts.googleapis.com/css2?family=Arimo:wght@400;700&family=Open+Sans:ital,wght@0,400;0,600;1,400&display=swap" rel="stylesheet">
<style>
  :root {
    --page: #2a2a2c;
    --blue-light: #0a90cf;
    --blue-mid: #1f5fb5;
    --blue-deep: #2b3684;
    --navy-text: #2b3a8c;
    --red: #c21f24;
    --red-dark: #7d1619;
    --cream: #efe9d6;
    --card-white: #f1f1f1;
    --ink: #1b1b1b;
    --silver: #e6e8ee;
  }
  * { margin: 0; padding: 0; box-sizing: border-box; }
  html, body { width: 1200px; height: 1138px; overflow: hidden; background: var(--page); }
  body { position: relative; font-family: "Arimo", Arial, sans-serif; }

  .card {
    position: absolute;
    border-radius: 14px;
    overflow: hidden;
    box-shadow: 0 4px 10px rgba(0,0,0,0.45);
  }

  /* Front */
  .card-front {
    left: 274px; top: 186px; width: 623px; height: 376px;
    background: linear-gradient(to bottom, var(--blue-light) 0%, var(--blue-mid) 55%, var(--blue-deep) 100%);
  }
  .front-mark {
    position: absolute; left: 236px; top: 70px; width: 148px; height: 148px;
    border-radius: 50%; background: var(--cream);
  }
  .front-name {
    position: absolute; left: 0; right: 0; top: 230px;
    text-align: center; font-family: "Arimo", Arial, sans-serif;
    font-size: 38px; font-weight: 400; color: var(--silver); letter-spacing: 1px;
  }
  .front-tagline {
    position: absolute; left: 0; right: 0; top: 277px;
    text-align: center; font-size: 19px; color: var(--silver); letter-spacing: 0.3px;
  }

  /* Back */
  .card-back {
    left: 276px; top: 608px; width: 618px; height: 374px;
    background: var(--card-white);
  }
  .back-waves { position: absolute; left: 0; top: 0; width: 618px; height: 200px; }
  .services {
    position: absolute; right: 28px; top: 18px; width: 320px;
    text-align: right; font-size: 16px; line-height: 19px; color: #fff;
  }
  .services strong { font-weight: 700; }
  .holder-name {
    position: absolute; left: 31px; top: 114px;
    font-family: "Open Sans", Arial, sans-serif; font-weight: 600;
    font-size: 24px; color: var(--navy-text);
  }
  .holder-quals {
    position: absolute; left: 31px; top: 142px; width: 300px;
    font-family: "Open Sans", Arial, sans-serif; font-style: italic;
    font-size: 15px; line-height: 21px; color: var(--navy-text);
  }
  .contacts { position: absolute; left: 31px; top: 240px; list-style: none; }
  .contacts li {
    display: flex; align-items: center; height: 23px;
    font-family: "Open Sans", Arial, sans-serif; font-size: 16px; color: var(--navy-text);
  }
  .contacts svg { width: 14px; height: 14px; margin-right: 16px; }
  .back-mark {
    position: absolute; left: 722px; left: 436px; top: 248px; width: 120px; height: 120px;
  }
  .back-mark-circle {
    position: absolute; left: 446px; top: 212px; width: 100px; height: 100px;
    border-radius: 50%; background: var(--cream);
  }
  .back-name {
    position: absolute; left: 396px; width: 200px; top: 316px;
    text-align: center; font-size: 16px; color: var(--navy-text);
  }
  .back-tagline {
    position: absolute; left: 31px; top: 330px;
    font-size: 16px; color: var(--ink);
  }
  .back-name { display: none; }
</style>
</head>
<body>

  <section class="card card-front" aria-label="Card front">
    <div class="front-mark" aria-hidden="true"></div>
    <div class="front-name">JOLLY PAWS</div>
    <div class="front-tagline">HAPPY DOGS, HAPPY OWNERS</div>
  </section>

  <section class="card card-back" aria-label="Card back">
    <svg class="back-waves" viewBox="0 0 618 200" aria-hidden="true">
      <defs>
        <linearGradient id="headerBlue" x1="0" y1="0" x2="1" y2="0">
          <stop offset="0" stop-color="#0a8fcf"/>
          <stop offset="1" stop-color="#2b3684"/>
        </linearGradient>
      </defs>
      <path d="M0 0 H618 V122 C520 140 470 140 400 112 C300 60 180 20 0 58 Z" fill="url(#headerBlue)"/>
      <path d="M0 58 C180 20 300 60 400 112 C470 140 520 140 618 122 V130 C520 148 460 150 390 124 C290 80 170 40 0 72 Z" fill="#ffffff"/>
      <path d="M0 68 C160 30 260 40 330 62 C200 40 100 54 0 88 Z" fill="var(--red-dark)"/>
      <path d="M40 82 C200 34 320 70 420 130 C480 160 540 158 618 140 V146 C540 166 470 166 410 138 C320 90 200 50 40 82 Z" fill="var(--red)"/>
    </svg>

    <p class="services"><strong>SERVICES:</strong> Providing Individual Coaching Strategies to Create Happy, Healthy and Social Canine Companions</p>

    <h1 class="holder-name">Denise Carvell</h1>
    <p class="holder-quals">Qualified in Dog Behavioural Training, Natural Animal Healthcare and Animal Health Science</p>

    <ul class="contacts">
      <li>
        <svg viewBox="0 0 14 14" aria-hidden="true"><rect x="3" y="0.5" width="8" height="13" rx="1.5" fill="none" stroke="#c21f24" stroke-width="1.4"/><rect x="4.6" y="2.2" width="4.8" height="5" fill="#c21f24"/></svg>
        0412 786 305
      </li>
      <li>
        <svg viewBox="0 0 14 14" aria-hidden="true"><rect x="0.5" y="3" width="13" height="9" fill="#c21f24"/><path d="M0.5 3 L7 8 L13.5 3" fill="none" stroke="#f1f1f1" stroke-width="1.2"/></svg>
        jollypaws1@mail.com
      </li>
    </ul>

    <div class="back-mark-circle" aria-hidden="true"></div>
    <div class="back-name">Jolly Paws</div>

    <p class="back-tagline">Promoting communication and connection between dogs and their families</p>
  </section>

</body>
</html>
```